New Business Card Design Project

We require a business card design for Vexalund, a newly established Indian company.
Our focus is on the development, manufacturing, and export of a diverse array of pharmaceutical products on a global scale. The card should convey a professional appearance, as our primary markets are in Africa, China, and Southeast Asian nations.
We envision a two-sided business card, with the reverse side dedicated to a logo set against a solid color or an elegantly designed pattern. The corners should be rounded. We would appreciate seeing both horizontal and vertical design options. We trust the designer to utilize their expertise in creating this design.

The content for the business card is included in the attached Word file.

Target Market(s)

Our primary markets are in Africa, China, and Southeast Asian, Latin America, Maldives, Sri Lanka

Industry/Entity Type

Pharmaceutical Manufacturing and Export

Contact Information for Business Card

Colors

Designer to choose colors to be used in the design.

Requirements
Must have
• The reverse side of the business card features solely the logo along with the tagline, "Care in Every Dose."
Should not have
• The logo should not exceed two instances, encompassing both the front and back sides of the card.

```html
<!DOCTYPE html>
<html lang="en">
<head>
<meta charset="utf-8">
<title>Vexalund Business Card</title>
<link rel="stylesheet" href="https://fonts.googleapis.com/css2?family=Montserrat:wght@400;500;700;800&family=Open+Sans:wght@400;600&display=swap">
<style>
  :root {
    --stage: #232323;
    --brand-blue: #2fa7df;
    --accent-red: #f0614b;
    --paper: #ffffff;
    --ink: #1e1e1e;
    --card-shadow: rgba(0, 0, 0, 0.55);
  }
  * { box-sizing: border-box; margin: 0; padding: 0; }
  html, body {
    width: 1200px;
    height: 780px;
    overflow: hidden;
    background: var(--stage);
  }
  .stage {
    width: 1200px;
    height: 780px;
    display: flex;
    align-items: center;
    justify-content: center;
    gap: 40px;
  }
  .card {
    position: relative;
    width: 540px;
    height: 310px;
    border-radius: 22px;
    overflow: hidden;
    box-shadow: 0 14px 30px var(--card-shadow);
  }

  /* Reverse side */
  .card--back {
    background: var(--brand-blue);
    display: flex;
    flex-direction: column;
    align-items: center;
    justify-content: center;
    color: var(--paper);
  }
  .brand-lockup {
    display: flex;
    align-items: center;
    gap: 14px;
  }
  .brand-dot {
    width: 26px;
    height: 26px;
    border-radius: 50%;
    background: var(--paper);
  }
  .brand-name {
    font-family: "Montserrat", sans-serif;
    font-weight: 800;
    font-size: 64px;
    letter-spacing: -0.5px;
    line-height: 1;
  }
  .tagline {
    margin-top: 22px;
    font-family: "Montserrat", sans-serif;
    font-weight: 400;
    font-size: 15px;
    letter-spacing: 1px;
  }

  /* Front side */
  .card--front {
    background: var(--paper);
    color: var(--ink);
  }
  .edge-tab {
    position: absolute;
    top: 0;
    right: 0;
    width: 18px;
    height: 66px;
    background: var(--brand-blue);
  }
  .person {
    position: absolute;
    top: 26px;
    right: 38px;
    text-align right;
    text-align: right;
    font-family: "Montserrat", sans-serif;
  }
  .person__name {
    font-size: 26px;
    line-height: 1.1;
  }
  .person__first {
    font-weight: 700;
    color: var(--brand-blue);
  }
  .person__last {
    font-weight: 400;
    color: var(--accent-red);
  }
  .person__role {
    margin-top: 4px;
    font-size: 13px;
    font-weight: 500;
    letter-spacing: 0.5px;
  }
  .front-brand {
    position: absolute;
    left: 34px;
    top: 104px;
    display: flex;
    align-items: center;
    gap: 10px;
  }
  .front-brand .brand-dot {
    width: 18px;
    height: 18px;
    background: var(--accent-red);
  }
  .front-brand .brand-name {
    font-size: 42px;
    color: var(--brand-blue);
  }
  .details {
    position: absolute;
    left: 36px;
    bottom: 26px;
    font-family: "Open Sans", sans-serif;
    font-size: 13px;
    line-height: 1.45;
  }
  .address {
    margin-bottom: 10px;
  }
  .contact-list {
    list-style: none;
  }
  .contact-list li {
    display: flex;
    align-items: center;
    gap: 9px;
  }
  .contact-icon {
    width: 13px;
    height: 13px;
    flex: none;
  }
</style>
</head>
<body>
<main class="stage">

  <section class="card card--back" aria-label="Card reverse side">
    <div class="brand-lockup">
      <span class="brand-dot"></span>
      <span class="brand-name">Vexalund</span>
    </div>
    <p class="tagline">Care in Every Dose.</p>
  </section>

  <section class="card card--front" aria-label="Card front side">
    <span class="edge-tab"></span>

    <div class="person">
      <p class="person__name"><span class="person__first">Arjun</span> <span class="person__last">K. Mehra</span></p>
      <p class="person__role">CEO</p>
    </div>

    <div class="front-brand">
      <span class="brand-dot"></span>
      <span class="brand-name">Vexalund</span>
    </div>

    <div class="details">
      <p class="address">14, Neelkamal Nagar,<br>Akola, 444001, India</p>
      <ul class="contact-list">
        <li>
          <svg class="contact-icon" viewBox="0 0 14 14" aria-hidden="true">
            <rect x="3" y="1" width="8" height="12" rx="1.5" fill="none" stroke="#f0614b" stroke-width="1.5"/>
          </svg>
          <span>+919 555018734</span>
        </li>
        <li>
          <svg class="contact-icon" viewBox="0 0 14 14" aria-hidden="true">
            <circle cx="7" cy="7" r="6" fill="none" stroke="#2fa7df" stroke-width="1.4"/>
            <ellipse cx="7" cy="7" rx="2.6" ry="6" fill="none" stroke="#2fa7df" stroke-width="1.1"/>
            <line x1="1" y1="7" x2="13" y2="7" stroke="#2fa7df" stroke-width="1.1"/>
          </svg>
          <span>www.vexalund.com</span>
        </li>
        <li>
          <svg class="contact-icon" viewBox="0 0 14 14" aria-hidden="true">
            <rect x="1" y="3" width="12" height="9" rx="1" fill="none" stroke="#f0614b" stroke-width="1.4"/>
            <polyline points="1.5,3.5 7,8 12.5,3.5" fill="none" stroke="#f0614b" stroke-width="1.4"/>
          </svg>
          <span>amehra@vexalund.com</span>
        </li>
      </ul>
    </div>
  </section>

</main>
</body>
</html>
```